VENTURE CAPITAL GROUP BUSINESS CARD DESIGN

Venture Capital Group based in SF looking for a bold business card design. No trendy colour explosion, 3D effects etc. Just "simple" optical effects. Works on your brain, keeps your eye focused and sticks to your mind.
Target Market(s)
Technology startups
Industry/Entity Type
Venture Capital
Contact Information for Business Card
DESMOND WHITLAKE
MANAGING PARTNER
187 FENWORTH ST SAN FRANCISCO, CA 94187
415.555.0142 O
415.555.0147 F
415.555.0193 C
desmond@veldtmoorcapital.ventures

```html
<!DOCTYPE html>
<html lang="en">
<head>
<meta charset="utf-8">
<title>Veldtmoor Capital Group – Business Card</title>
<link rel="stylesheet" href="https://fonts.googleapis.com/css2?family=EB+Garamond:wght@400;500;700&display=swap">
<style>
  :root {
    --stage: #2a2a2a;
    --green-deep: #0f5a1c;
    --green-mid: #1f8a2e;
    --green-bright: #3fae45;
    --brand-green: #2e9a3a;
    --card-dark: #232323;
    --card-dark-2: #303030;
    --text-light: #e6e6e6;
    --text-muted: #bdbdbd;
    --white: #ffffff;
  }
  * { box-sizing: border-box; margin: 0; padding: 0; }
  html, body {
    width: 1200px; height: 873px; overflow: hidden;
    background: var(--stage);
    font-family: "EB Garamond", Georgia, serif;
  }
  .stage {
    position: relative; width: 1200px; height: 873px;
    display: flex; align-items: center; justify-content: center; gap: 40px;
  }
  .card {
    position: relative; width: 540px; height: 309px;
    border-radius: 3px; overflow: hidden;
    box-shadow: 0 14px 30px rgba(0,0,0,.45);
  }

  /* Front */
  .card--front {
    background: radial-gradient(ellipse at 55% 45%, var(--green-bright) 0%, var(--green-mid) 45%, var(--green-deep) 100%);
    display: flex; align-items: center; justify-content: center;
  }
  .wordmark { display: flex; align-items: center; gap: 12px; }
  .wordmark__dot { width: 18px; height: 18px; border-radius: 50%; }
  .wordmark__name {
    font-weight: 500; text-transform: uppercase; letter-spacing: .08em; line-height: 1.05;
    text-align: left;
  }
  .card--front .wordmark__dot { background: var(--white); }
  .card--front .wordmark__name { color: var(--white); font-size: 34px; }
  .card--front .wordmark__name small { display: block; font-size: 15px; letter-spacing: .42em; }

  /* Back */
  .card--back {
    background: linear-gradient(150deg, var(--card-dark-2) 0%, var(--card-dark) 55%, #1b1b1b 100%);
  }
  .card--back .pattern {
    position: absolute; inset: 0;
    background: linear-gradient(120deg, rgba(255,255,255,.03) 0%, rgba(0,0,0,.06) 50%, rgba(255,255,255,.02) 100%);
  }
  .holder { position: absolute; top: 22px; left: 0; right: 0; text-align: center; }
  .holder__name { color: var(--brand-green); font-weight: 700; font-size: 22px; letter-spacing: .01em; }
  .holder__title { color: var(--text-light); font-size: 12px; margin-top: 1px; }

  .card--back .wordmark { position: absolute; left: 40px; top: 150px; gap: 10px; }
  .card--back .wordmark__dot { background: var(--brand-green); width: 14px; height: 14px; }
  .card--back .wordmark__name { color: var(--brand-green); font-size: 27px; }
  .card--back .wordmark__name small { display: block; font-size: 12px; letter-spacing: .42em; }

  .divider {
    position: absolute; left: 282px; top: 92px; width: 2px; height: 130px;
    background: linear-gradient(180deg, rgba(255,255,255,0), rgba(255,255,255,.55), rgba(255,255,255,0));
  }
  .contacts { position: absolute; left: 302px; top: 96px; list-style: none; }
  .contacts li {
    display: flex; align-items: center; gap: 8px;
    color: var(--text-light); font-size: 13.5px; height: 23px;
  }
  .contacts li.gap { margin-top: 6px; }
  .icon {
    width: 17px; height: 17px; border-radius: 50%; background: var(--brand-green);
    display: inline-flex; align-items: center; justify-content: center; flex: none;
  }
  .icon svg { width: 10px; height: 10px; fill: var(--white); }
  .website {
    position: absolute; bottom: 22px; left: 0; right: 0; text-align: center;
    color: var(--text-muted); font-size: 14px; letter-spacing: .22em;
  }
</style>
</head>
<body>
<main class="stage">

  <section class="card card--front" aria-label="Business card front">
    <div class="wordmark">
      <span class="wordmark__dot"></span>
      <p class="wordmark__name">Veldtmoor<small>Capital Group</small></p>
    </div>
  </section>

  <section class="card card--back" aria-label="Business card back">
    <div class="pattern" role="img" aria-label="Faint dark low-poly facet texture"></div>

    <header class="holder">
      <h1 class="holder__name">Desmond Whitlake</h1>
      <p class="holder__title">Managing Partner</p>
    </header>

    <div class="wordmark">
      <span class="wordmark__dot"></span>
      <p class="wordmark__name">Veldtmoor<small>Capital Group</small></p>
    </div>

    <div class="divider"></div>

    <ul class="contacts">
      <li><span class="icon"><svg viewBox="0 0 10 10"><path d="M1 4c0-2 2-3 4-3s4 1 4 3H7V3H3v1zM2 5h6l1 4H1z"/></svg></span>415.555.0142</li>
      <li><span class="icon"><svg viewBox="0 0 10 10"><path d="M3 1h4v2H3zM1 4h8v4H7V6H3v2H1zM3 7h4v2H3z"/></svg></span>415.555.0147</li>
      <li><span class="icon"><svg viewBox="0 0 10 10"><path d="M2 1l2 0 1 2-1 1c.6 1.2 1.3 1.9 2 2l1-1 2 1v2c-4 0-7-3-7-7z"/></svg></span>415.555.0193</li>
      <li class="gap"><span class="icon"><svg viewBox="0 0 10 10"><path d="M1 2h8v6H1zM1.6 2.6L5 5.4l3.4-2.8v.9L5 6.3 1.6 3.5z" fill-rule="evenodd"/></svg></span>desmond@veldtmoorcapital.ventures</li>
      <li><span class="icon"><svg viewBox="0 0 10 10"><path d="M5 .5a3 3 0 0 1 3 3c0 2.2-3 6-3 6s-3-3.8-3-6a3 3 0 0 1 3-3zm0 2a1 1 0 1 0 0 2 1 1 0 0 0 0-2z" fill-rule="evenodd"/></svg></span>187 Fenworth St San Francisco, CA 94187</li>
    </ul>

    <p class="website">www.veldtmoorcapital.ventures</p>
  </section>

</main>
</body>
</html>
```